Specialised investor in e-mobility and energy wants business card design

We need a business card design that fits our existing corporate design. <The look and feel must be 'sharp'/'clean', dynamic, communicate momentum, professionalism etc (as one would imagine from a firm in the financial sector). We like the idea of a reverse-side of the card that includes the logo, and the name and contact details on the other. We expect the deliverable to be whatever format might be required to be able to get cards printed directly by a service such as kelmo press. Our website is www.zub.capital

```html
<!DOCTYPE html>
<html lang="en">
<head>
<meta charset="utf-8">
<title>Zub Capital — Business Card</title>
<link href="https://fonts.googleapis.com/css2?family=Montserrat:wght@400;500;700&display=swap" rel="stylesheet">
<style>
  :root {
    --forest: #2f5124;
    --leaf: #7ab648;
    --paper: #ffffff;
    --ground: #eceeea;
    --ink-light: #ffffff;
  }
  * { margin: 0; padding: 0; box-sizing: border-box; }
  html, body { width: 1200px; height: 960px; overflow: hidden; }
  body {
    background: var(--ground);
    font-family: "Montserrat", sans-serif;
    position: relative;
  }
  .card {
    position: absolute;
    left: 290px;
    width: 620px;
    height: 380px;
    background: var(--paper);
    border-radius: 28px;
    overflow: hidden;
    box-shadow: 0 6px 18px rgba(0,0,0,0.12);
  }
  .card--front { top: 60px; }
  .card--back { top: 520px; }

  .wordmark {
    font-family: "Montserrat", sans-serif;
    font-weight: 500;
    color: var(--forest);
    display: flex;
    align-items: center;
    gap: 14px;
    white-space: nowrap;
  }
  .wordmark__dot {
    width: 18px; height: 18px;
    border-radius: 50%;
    background: var(--forest);
  }
  .card--front .wordmark {
    position: absolute;
    left: 50%; top: 50%;
    transform: translate(-50%, -50%);
    font-size: 70px;
  }
  .card--back .wordmark--corner {
    position: absolute;
    left: 38px; top: 52px;
    font-size: 40px;
    gap: 10px;
  }
  .card--back .wordmark--corner .wordmark__dot { width: 12px; height: 12px; }

  .back-shape { position: absolute; inset: 0; }

  .wordmark--reverse {
    position: absolute;
    left: 262px; top: 238px;
    font-size: 30px;
    color: var(--ink-light);
    gap: 0;
  }

  .divider {
    position: absolute;
    left: 392px; top: 150px;
    width: 2px; height: 195px;
    background: var(--ink-light);
  }
  .contact {
    position: absolute;
    left: 408px; top: 150px;
    color: var(--ink-light);
    font-size: 14px;
    line-height: 1.55;
  }
  .contact__name {
    font-weight: 700;
    font-size: 20px;
    color: var(--leaf);
    letter-spacing: 0.5px;
    text-transform: uppercase;
    line-height: 1.2;
  }
  .contact__role { margin-bottom: 10px; }
  .contact__line { display: flex; align-items: center; gap: 8px; }
  .contact__line svg { width: 12px; height: 12px; fill: var(--ink-light); flex: none; }
  .contact__company { color: var(--leaf); margin-top: 10px; }
</style>
</head>
<body>

  <section class="card card--front" aria-label="Card front">
    <div class="wordmark"><span class="wordmark__dot"></span>Zub Capital</div>
  </section>

  <section class="card card--back" aria-label="Card back">
    <svg class="back-shape" viewBox="0 0 620 380" preserveAspectRatio="none" aria-hidden="true">
      <path d="M452 0 C312 70 238 220 214 380" fill="none" stroke="var(--leaf)" stroke-width="9"/>
      <path d="M470 0 C330 70 256 220 232 380 L620 380 L620 0 Z" fill="var(--forest)"/>
    </svg>

    <div class="wordmark wordmark--corner"><span class="wordmark__dot"></span>Zub Capital</div>

    <div class="wordmark wordmark--reverse">Zub</div>

    <div class="divider"></div>

    <div class="contact">
      <div class="contact__name">Mara Ellison</div>
      <div class="contact__role">Managing Director</div>
      <div class="contact__line">
        <svg viewBox="0 0 24 24"><path d="M6.6 10.8a15 15 0 0 0 6.6 6.6l2.2-2.2a1 1 0 0 1 1-.25 11.4 11.4 0 0 0 3.6.57 1 1 0 0 1 1 1V20a1 1 0 0 1-1 1A17 17 0 0 1 3 4a1 1 0 0 1 1-1h3.5a1 1 0 0 1 1 1c0 1.25.2 2.45.57 3.6a1 1 0 0 1-.25 1z"/></svg>
        +41 79555 0142
      </div>
      <div class="contact__line">
        <svg viewBox="0 0 24 24"><path d="M2 5h20v14H2z M2 5l10 8 10-8" /></svg>
        mara@zub.capital
      </div>
      <div class="contact__line">
        <svg viewBox="0 0 24 24"><circle cx="12" cy="12" r="10"/></svg>
        www.zub.capital
      </div>
      <div class="contact__company">Zub Capital S.A.</div>
      <div>Geneva, Switzerland</div>
    </div>
  </section>

</body>
</html>
```